Mortgage Broking Flyer to attract attention

We are looking for double sided, colour DL sized flyers for a mail drop to inform people what services we offer.
We are a Mortgage Broking Business in Alice Springs NT Australia. Alice Springs is a large country town so we want something that is personal, a little bit playful but still professional, and is going to capture the attention of potential clients when they first look at it so they want to read on.
Please use our logo and colours (red & white) plus a photo of our team – all attached.
Brochure Front: IMPORTANT
Please come up with a tag line based on the following-We want to be seen as different to the bank, more friendly, personable, we listen, want to help and want people to keep coming back even for the little things.
The home page from our website has good dot points but we would like them shorter and to the point www.ochrecrestlending.com.au
Plus include something which lets customer know that we can assist purchases made through any real estate office, anywhere in Australia
Don’t want the front to contain too many long sentences or paragraphs.
Brochure Back:
Please include:
Services/Specialties
• First home buyers
• Refinancing
• Investments
• Construction loans
• Debt consolidation
• Commercial finance
Please include the following contact details:
Dominic Farrow – Managing Director
Prudence Wexley – Loans Consultant
Maeve Dunleavy – Loans Consultant
Suite 4/17 Corbel Street, Alice Springs NT 0870
Phone: 08 8961 4728
www.ochrecrestlending.com.au
We must include the following fine print at the back/bottom of the brochure:
Dominic Farrow (Credit Representative Number: 527814), Prudence Wexley (Credit Representative Number: 527813) and Maeve Dunleavy (Credit Representative Number: 613290) are credit representatives of QMTRV Pty Ltd (Australian Credit Licence Number: 458906)
Please feel free to email me with any questions.
maeve@ochrecrestlending.com.au

```html
<!DOCTYPE html>
<html lang="en">
<head>
<meta charset="utf-8">
<title>Ochrecrest Lending – Flyer Front</title>
<link rel="stylesheet" href="https://fonts.googleapis.com/css2?family=Inter:wght@200;300;400;700;800&display=swap">
<style>
  :root {
    --brand-red: #e1262c;
    --white: #ffffff;
    --sky-top: #b9b4c4;
    --sky-low: #c9a99a;
    --ridge: #b8674a;
    --scrub-gold: #c98f2e;
    --scrub-olive: #7a7a3a;
  }
  * { margin: 0; padding: 0; box-sizing: border-box; }
  html, body { width: 1200px; height: 573px; overflow: hidden; background: var(--white); }
  .flyer {
    position: relative;
    width: 1200px;
    height: 573px;
    overflow: hidden;
    font-family: "Inter", "Helvetica Neue", Arial, sans-serif;
    color: var(--white);
  }
  .landscape {
    position: absolute;
    inset: 0 0 128px 0;
    background:
      linear-gradient(200deg, rgba(190,100,70,0.0) 35%, rgba(184,103,74,0.55) 55%, rgba(120,110,60,0.35) 80%),
      radial-gradient(ellipse 70% 60% at 18% 95%, var(--scrub-gold) 0%, rgba(201,143,46,0.6) 45%, transparent 75%),
      linear-gradient(180deg, var(--sky-top) 0%, var(--sky-low) 22%, #9c8a86 40%, var(--ridge) 62%, var(--scrub-olive) 100%);
  }
  .tagline {
    position: absolute;
    left: 52px;
    top: 22px;
    right: 40px;
    text-transform: uppercase;
    text-shadow: 0 1px 6px rgba(0,0,0,0.15);
  }
  .tagline__lead {
    font-weight: 800;
    font-size: 22px;
    letter-spacing: 0.5px;
    line-height: 1;
  }
  .tagline__outline {
    margin-top: 14px;
    font-weight: 700;
    font-size: 88px;
    line-height: 1;
    letter-spacing: 1px;
    color: transparent;
    -webkit-text-stroke: 2px var(--white);
    text-shadow: none;
  }
  .tagline__line {
    font-size: 94px;
    line-height: 1;
    margin-top: 4px;
    letter-spacing: -0.5px;
  }
  .tagline__light { font-weight: 200; }
  .tagline__strong { font-weight: 800; }
  .tagline__close {
    margin-top: 14px;
    font-weight: 800;
    font-size: 20.5px;
    line-height: 1;
    letter-spacing: 0.2px;
  }
  .coverage {
    position: absolute;
    left: 0;
    right: 0;
    bottom: 0;
    height: 128px;
    background: var(--brand-red);
  }
  .coverage__text {
    position: absolute;
    left: 52px;
    top: 42px;
    font-size: 21px;
    font-weight: 300;
    line-height: 30px;
    text-transform: uppercase;
  }
  .coverage__text strong { font-weight: 800; }
  .brand {
    position: absolute;
    right: 20px;
    top: 18px;
    display: flex;
    align-items: center;
    gap: 14px;
  }
  .brand__name {
    font-size: 20px;
    font-weight: 800;
    color: var(--white);
    text-transform: uppercase;
    text-align: right;
    line-height: 1.15;
  }
  .brand__mark { width: 92px; height: 92px; display: block; }
</style>
</head>
<body>
  <main class="flyer">
    <div class="landscape" role="img" aria-label="Photograph of the MacDonnell Ranges at sunset above golden bushland near Alice Springs"></div>

    <section class="tagline">
      <p class="tagline__lead">Different to the bank...</p>
      <h1 class="tagline__outline">We listen &amp; help</h1>
      <p class="tagline__line"><span class="tagline__light">More </span><span class="tagline__strong">Friendly</span></p>
      <p class="tagline__line"><span class="tagline__light">More </span><span class="tagline__strong">Personable</span></p>
      <p class="tagline__close">...and want people to keep coming back even for the little things.</p>
    </section>

    <footer class="coverage">
      <p class="coverage__text">We can assist purchases made through<br>any real estate office, <strong>anywhere in Australia</strong></p>
      <div class="brand">
        <span class="brand__name">Ochrecrest<br>Lending</span>
        <svg class="brand__mark" viewBox="0 0 92 92" aria-hidden="true">
          <circle cx="46" cy="46" r="45" fill="#ffffff"/>
        </svg>
      </div>
    </footer>
  </main>
</body>
</html>
```